Coastline Premier Retreats Business Card Design

Design a business card for Coastline Premier Retreats. Look at the website for colors and reference. Card should have logo, name, title, office number, mobile number, email, URL and a tagline like, "Luxury Hotel & Resort Email Marketing" (This might change).

https://www.coastlinepremierretreats.example

The rest I will leave up to your imagination.

Contact Information for Business Card

Logo, name, title, office number, mobile number, email, URL and a tagline like, "Luxury Hotel & Resort Email Marketing" (This might change).

```html
<!DOCTYPE html>
<html lang="en">
<head>
<meta charset="utf-8">
<title>Coastline Premier Retreats – Business Card</title>
<link rel="stylesheet" href="https://fonts.googleapis.com/css2?family=Montserrat:wght@400;600;800&display=swap">
<style>
  :root {
    --stage: #3a3a3a;
    --card: #1b1b1b;
    --accent: #f07a10;
    --ink: #ffffff;
    --ink-soft: #e9e9e9;
  }
  * { box-sizing: border-box; margin: 0; padding: 0; }
  html, body {
    width: 1200px; height: 900px; overflow: hidden;
    background: var(--stage);
    font-family: "Montserrat", Arial, sans-serif;
  }
  .stage {
    width: 1200px; height: 900px;
    display: flex; flex-direction: column; align-items: center; justify-content: center;
    gap: 40px;
  }
  .card {
    position: relative;
    width: 700px; height: 400px;
    background: var(--card);
    border-bottom: 5px solid var(--accent);
    border-left: 3px solid var(--accent);
    box-shadow: 0 14px 30px rgba(0,0,0,.45);
    overflow: hidden;
  }
  .brand {
    display: flex; align-items: center; gap: 14px;
    color: var(--ink);
    font-weight: 800;
    text-transform: uppercase;
    letter-spacing: 1px;
    line-height: 1.05;
  }
  .brand__square {
    width: 16px; height: 16px; background: var(--accent); flex: none;
  }
  /* front */
  .card--front .brand {
    position: absolute; left: 0; right: 0; top: 130px;
    justify-content: center;
    font-size: 38px;
  }
  .card--front .brand__square { width: 22px; height: 22px; }
  .tagline {
    position: absolute; left: 0; right: 0; bottom: 70px;
    text-align: center;
    color: var(--accent);
    font-size: 19px; font-weight: 400; letter-spacing: .6px;
  }
  /* back */
  .card--back .brand {
    position: absolute; left: 48px; top: 60px;
    font-size: 22px;
  }
  .person {
    position: absolute; right: 48px; top: 150px; text-align: right;
  }
  .person__name {
    color: var(--accent);
    font-size: 30px; font-weight: 800; letter-spacing: 1px; text-transform: uppercase;
  }
  .person__title {
    color: var(--ink-soft); font-size: 15px; margin-top: 2px;
  }
  .divider {
    position: absolute; left: 150px; right: 32px; top: 232px;
    height: 1px; background: var(--accent);
  }
  .contacts {
    position: absolute; left: 170px; top: 252px;
    list-style: none;
    color: var(--ink-soft); font-size: 15px; line-height: 26px;
  }
  .contacts li { display: flex; align-items: center; gap: 10px; }
  .contacts svg { width: 14px; height: 14px; flex: none; }
  .address {
    position: absolute; right: 48px; top: 262px; text-align: right;
    color: var(--ink-soft); font-size: 15px; line-height: 24px;
  }
</style>
</head>
<body>
<main class="stage">
  <section class="card card--front" aria-label="Card front">
    <div class="brand"><span class="brand__square"></span><span>Coastline Premier Retreats</span></div>
    <p class="tagline">Luxury Hotel &amp; Resort Email Marketing</p>
  </section>

  <section class="card card--back" aria-label="Card back">
    <div class="brand"><span class="brand__square"></span><span>Coastline Premier Retreats</span></div>
    <div class="person">
      <p class="person__name">Daniel Brooks</p>
      <p class="person__title">CEO/Founder</p>
    </div>
    <div class="divider"></div>
    <ul class="contacts">
      <li>
        <svg viewBox="0 0 14 14" aria-hidden="true"><rect x="4" y="1" width="6" height="12" rx="1" fill="none" stroke="#f07a10" stroke-width="1.4"/><circle cx="7" cy="11" r=".8" fill="#f07a10"/></svg>
        555.014.2300
      </li>
      <li>
        <svg viewBox="0 0 14 14" aria-hidden="true"><path d="M2 5 Q7 1 12 5 L11 7 L9 6 L9 5 Q7 4 5 5 L5 6 L3 7 Z" fill="#f07a10"/><rect x="3" y="8" width="8" height="4" rx="1" fill="#f07a10"/></svg>
        +34 611 204 387
      </li>
      <li>
        <svg viewBox="0 0 14 14" aria-hidden="true"><rect x="1" y="3" width="12" height="8" fill="none" stroke="#f07a10" stroke-width="1.4"/><path d="M1 3 L7 8 L13 3" fill="none" stroke="#f07a10" stroke-width="1.4"/></svg>
        info@coastlinepremierretreats.example
      </li>
      <li>
        <svg viewBox="0 0 14 14" aria-hidden="true"><circle cx="7" cy="7" r="5.5" fill="none" stroke="#f07a10" stroke-width="1.4"/><path d="M1.5 7 H12.5 M7 1.5 Q3.5 7 7 12.5 Q10.5 7 7 1.5" fill="none" stroke="#f07a10" stroke-width="1.1"/></svg>
        www.coastlinepremierretreats.example
      </li>
    </ul>
    <address class="address" style="font-style:normal">
      PO Box, 480 Harbor Rd<br>
      Bayview, ST 40512
    </address>
  </section>
</main>
</body>
</html>
```